Harlow Cargomax Wrap- Pool Service Company

Looking for full vehicle wrap and half vehicle wrap designs for my swimming pool service and repair company Wren Basins LLC. Had a logo designed on here which came out great so hoping for an awesome van wrap too. I want it to have my logo in the design as well as something to do with pools and water, so you can instantly tell it is a swimming pool company at a quick glance. Plus the company information listed. This is a relatively new company so at the moment we only specialize in Pool Service and Repair, Pool Inspections, and Pool Safety Covers. I would like the design to be made so it does not focus on just listing the services allowing it to last many years as our services expand. I have attached a copy of my logo. Please let me know if anything else is needed. This will be going on a Harlow Cargomax 250 148" Medium roof van.
Target Market(s)
high income pool owners
Requirements
Must have
- Logo
Swimming pool look and feel
Pool Service and Repair, Pool Inspections, Safety Covers ...AND MORE!
555-214-8690
www.WrenBasinsQT.example
Nice to have
- Something very eye catching that grabs attention. Should be able to easily read everything without a lot of clutter or clash.

```html
<!DOCTYPE html>
<html lang="en">
<head>
<meta charset="utf-8">
<title>Wren Basins LLC – Van Wrap</title>
<link rel="stylesheet" href="https://fonts.googleapis.com/css2?family=Raleway:ital,wght@0,800;1,800;1,900&family=Oswald:wght@500&display=swap">
<style>
  :root {
    --bg: #edebeb;
    --orange: #f23d12;
    --blue: #1f98c2;
    --blue-deep: #1784ad;
    --navy: #1c2a63;
    --white: #ffffff;
    --red: #d7301a;
    --outline: #c8c5c2;
    --water-light: #9fdcf0;
    --water-mid: #4fb8df;
  }
  html, body {
    margin: 0;
    width: 1200px;
    height: 618px;
    overflow: hidden;
    background: var(--bg);
  }
  .canvas {
    position: relative;
    width: 1200px;
    height: 618px;
  }
  .palette-dots {
    position: absolute;
    top: 24px;
    right: 32px;
    display: flex;
    gap: 12px;
  }
  .palette-dots span {
    width: 25px;
    height: 25px;
    border-radius: 50%;
  }
  .dot-orange { background: var(--orange); }
  .dot-blue { background: var(--blue); }
  .dot-white { background: var(--white); }
  .van {
    position: absolute;
    inset: 0;
    filter: drop-shadow(0 6px 8px rgba(0,0,0,0.12));
  }
  .headline-box-text {
    font-family: "Raleway", sans-serif;
    font-style: italic;
    font-weight: 900;
    fill: var(--blue);
  }
  .headline-white {
    font-family: "Raleway", sans-serif;
    font-style: italic;
    font-weight: 900;
    fill: var(--white);
  }
  .services {
    font-family: "Raleway", sans-serif;
    font-style: italic;
    font-weight: 800;
    font-size: 15.5px;
    fill: var(--white);
  }
  .contact {
    font-family: "Oswald", sans-serif;
    font-weight: 500;
    fill: var(--white);
  }
  .brand-name {
    font-family: "Raleway", sans-serif;
    font-weight: 800;
    font-size: 21px;
    fill: var(--navy);
    letter-spacing: 0.5px;
  }
</style>
</head>
<body>
<div class="canvas">
  <div class="palette-dots">
    <span class="dot-orange"></span>
    <span class="dot-blue"></span>
    <span class="dot-white"></span>
  </div>

  <svg class="van" width="1200" height="618" viewBox="0 0 1200 618" xmlns="http://www.w3.org/2000/svg">
    <defs>
      <clipPath id="van-body">
        <path d="M494,172 L1006,182 Q1022,184 1022,200 L1022,348 L1004,356 L1004,438 L906,436 C896,414 830,414 819,436 L331,434 C318,405 238,400 225,423 L138,420 L138,388 L248,380 L250,322 L430,196 C450,180 470,172 494,172 Z"/>
      </clipPath>
      <linearGradient id="water-fill" x1="0" y1="1" x2="1" y2="0">
        <stop offset="0" stop-color="var(--water-mid)"/>
        <stop offset="1" stop-color="var(--water-light)"/>
      </linearGradient>
      <linearGradient id="blue-fill" x1="0" y1="0" x2="1" y2="1">
        <stop offset="0" stop-color="var(--blue)"/>
        <stop offset="1" stop-color="var(--blue-deep)"/>
      </linearGradient>
    </defs>

    <path class="van-outline" d="M494,167 L1008,177 Q1027,180 1027,200 L1027,351 L1009,359 L1009,443 L903,441 C893,420 833,420 822,441 L328,439 C314,411 242,407 228,428 L133,425 L133,383 L244,376 L246,319 L427,191 C448,175 470,167 494,167 Z" fill="var(--outline)"/>

    <g clip-path="url(#van-body)">
      <rect class="body-white" x="0" y="0" width="1200" height="618" fill="var(--white)"/>
      <path class="roof-band" d="M0,0 L700,0 L700,306 L300,296 L0,300 Z" fill="var(--orange)"/>
      <path class="side-panel" d="M603,165 C560,200 525,255 510,300 C508,318 540,322 566,334 C590,352 597,395 595,440 L1030,445 L1030,165 Z" fill="url(#blue-fill)"/>
      <path class="water-panel" role="img" aria-label="Pool water and tile texture" d="M760,440 C850,392 935,312 1030,282 L1030,445 Z" fill="url(#water-fill)"/>
    </g>

    <path class="side-window" d="M387,240 L455,237 Q461,238 460,245 L452,326 Q450,333 440,336 C390,350 320,356 250,359 Z" fill="var(--bg)" stroke="var(--outline)" stroke-width="4" stroke-linejoin="round"/>

    <g class="brand">
      <circle cx="496" cy="364" r="24" fill="var(--blue)"/>
      <text class="brand-name" x="494" y="417" text-anchor="middle">WREN BASINS</text>
    </g>

    <g class="headline" transform="rotate(2 745 250)">
      <rect x="613" y="223" width="272" height="55" rx="5" fill="var(--red)"/>
      <rect x="607" y="218" width="272" height="55" rx="5" fill="var(--white)"/>
      <text class="headline-box-text" x="743" y="265" font-size="43" text-anchor="middle">Pool Service</text>
    </g>
    <text class="headline-white" x="614" y="302" font-size="22" transform="rotate(2 614 302)">and</text>
    <text class="headline-white" x="660" y="340" font-size="62" transform="rotate(3 660 340)">Repair,</text>

    <g class="services" transform="rotate(4 650 365)">
      <text x="652" y="367">Pool Inspections,</text>
      <text x="650" y="387">Safety Covers</text>
      <text x="648" y="408">...AND MORE!</text>
    </g>

    <g class="contact-bands">
      <polygon points="878,374 1000,376 1000,397 860,396" fill="var(--red)"/>
      <text class="contact" x="990" y="393" font-size="19" text-anchor="end" textLength="116" lengthAdjust="spacingAndGlyphs" transform="skewX(-8) translate(55 0)">555-214-8690</text>
      <polygon points="836,402 1000,403 1000,421 819,420" fill="var(--red)"/>
      <text class="contact" x="990" y="417" font-size="13" text-anchor="end" textLength="138" lengthAdjust="spacingAndGlyphs" transform="skewX(-8) translate(59 0)">WWW.WRENBASINSQT.EXAMPLE</text>
    </g>
  </svg>
</div>
</body>
</html>
```